Business Card Design for Vandel Holdings

I need a business card designed for Vandel Holdings. I would like basic contact info and would like the card to be a bit modern but not childish. We manage several companies so it needs to look very professional. Watermark is cool and a plan logo maybe offset on the other side but I will leave the design up to you. I would like to see both color and grey scale designs. This is my first time using Pixel Harbor so hopefully we get some great results! Future projects available for the selected designer potentially.

Target Market(s)

Vandel Holdings owns several companies serving the software, real estate and automotive industry

Industry/Entity Type

Business

Contact Information for Business Card

Douglas R. Vandel
208.562.1437
douglas.r.vandel@mailnest.test

Font styles to use
Serif

Requirements
Must have
• contact information listed on card details
Nice to have
• I am open to letting you use your creative mind to design the best eye catching cards.

```html
<!DOCTYPE html>
<html lang="en">
<head>
<meta charset="utf-8">
<title>Vandel Holdings – Business Card</title>
<link rel="stylesheet" href="https://fonts.googleapis.com/css2?family=Libre+Baskerville:wght@400;700&display=swap">
<style>
  :root {
    --canvas-bg: #ececec;
    --card-white: #ffffff;
    --card-black: #000000;
    --brand-blue: #1a8fd0;
    --brand-sky: #2aa3dd;
    --brand-navy: #2c4a8c;
    --title-navy: #27418a;
    --ink: #111111;
    --mark-ring: #6fc3e3;
    --mark-core: #8b9cc0;
    --mark-ring-dark: #0b4e68;
    --mark-core-dark: #1a2a4e;
  }
  /* Greyscale edition of the same card, used for monochrome output */
  .theme-greyscale {
    --brand-blue: #3a3a3a;
    --brand-sky: #6a6a6a;
    --brand-navy: #2e2e2e;
    --title-navy: #444444;
    --mark-ring: #c4c4c4;
    --mark-core: #9e9e9e;
    --mark-ring-dark: #3c3c3c;
    --mark-core-dark: #242424;
  }
  @media (monochrome) {
    :root {
      --brand-blue: #3a3a3a;
      --brand-sky: #6a6a6a;
      --brand-navy: #2e2e2e;
      --title-navy: #444444;
      --mark-ring: #c4c4c4;
      --mark-core: #9e9e9e;
      --mark-ring-dark: #3c3c3c;
      --mark-core-dark: #242424;
    }
  }
  * { box-sizing: border-box; margin: 0; padding: 0; }
  html, body {
    width: 1200px; height: 586px; overflow: hidden;
    background: var(--canvas-bg);
    font-family: "Libre Baskerville", Georgia, serif;
  }
  .card {
    position: absolute; top: 130px;
    width: 492px; height: 298px; overflow: hidden;
  }
  .card-front { left: 66px; background: var(--card-white); }
  .card-back { left: 600px; width: 490px; background: var(--card-black); }

  .brand-lockup { position: absolute; display: flex; align-items: center; gap: 10px; }
  .brand-dot {
    border-radius: 50%; background: var(--brand-navy);
    border: 7px solid var(--brand-sky); flex: none;
  }
  .brand-name {
    font-weight: 700; color: var(--brand-sky); line-height: 1.2;
  }
  .card-front .brand-lockup { left: 26px; top: 16px; }
  .card-front .brand-dot { width: 84px; height: 84px; }
  .card-front .brand-name { font-size: 15px; }

  .watermark { position: absolute; border-radius: 50%; }
  .card-front .watermark {
    left: 328px; top: 12px; width: 280px; height: 280px;
    background: var(--mark-core); border: 22px solid var(--mark-ring);
  }
  .card-back .watermark {
    left: -104px; top: 15px; width: 272px; height: 272px;
    background: var(--mark-core-dark); border: 22px solid var(--mark-ring-dark);
  }

  .name-tab {
    position: absolute; left: 0; top: 151px; width: 6px; height: 30px;
    background: var(--brand-blue); border-radius: 0 4px 4px 0;
  }
  .person-name {
    position: absolute; left: 27px; top: 149px;
    font-size: 17px; font-weight: 700; color: var(--brand-blue);
    line-height: 1.2; white-space: nowrap;
  }
  .person-title {
    position: absolute; left: 27px; top: 172px;
    font-size: 11.5px; color: var(--title-navy); white-space: nowrap;
  }
  .contact-list { position: absolute; left: 30px; top: 235px; list-style: none; }
  .contact-item {
    display: flex; align-items: center; gap: 6px;
    font-size: 12px; color: var(--ink); height: 18px; margin-bottom: 10px;
    white-space: nowrap;
  }
  .contact-icon { width: 12px; height: 12px; flex: none; }
  .contact-icon .icon-disc { fill: var(--brand-blue); }

  .card-back .brand-lockup {
    left: 238px; width: 180px; top: 84px;
    flex-direction: column;
  }
  .card-back .brand-dot { width: 148px; height: 148px; border-width: 14px; }
  .card-back .brand-name { font-size: 15px; text-align: center; white-space: nowrap; }
</style>
</head>
<body>
  <section class="card card-front" aria-label="Card front">
    <div class="watermark" aria-hidden="true"></div>
    <div class="brand-lockup">
      <span class="brand-dot"></span>
      <span class="brand-name">Vandel<br>Holdings</span>
    </div>
    <span class="name-tab"></span>
    <h1 class="person-name">DOUGLAS R. VANDEL</h1>
    <p class="person-title">Managing Partner</p>
    <ul class="contact-list">
      <li class="contact-item">
        <svg class="contact-icon" viewBox="0 0 12 12" aria-hidden="true">
          <circle class="icon-disc" cx="6" cy="6" r="6"/>
          <path d="M3 4.2h6v1.2l-1.2.6V5H4.2v1l-1.2-.6z M3.6 6.6h4.8v2H3.6z" fill="#fff"/>
        </svg>
        208.562.1437
      </li>
      <li class="contact-item">
        <svg class="contact-icon" viewBox="0 0 12 12" aria-hidden="true">
          <circle class="icon-disc" cx="6" cy="6" r="6"/>
          <rect x="3" y="4" width="6" height="4.2" fill="#fff"/>
          <path d="M3 4l3 2.3L9 4" fill="none" stroke="#777" stroke-width="0.8"/>
        </svg>
        douglas.r.vandel@mailnest.test
      </li>
    </ul>
  </section>

  <section class="card card-back" aria-label="Card back">
    <div class="watermark" aria-hidden="true"></div>
    <div class="brand-lockup">
      <span class="brand-dot"></span>
      <span class="brand-name">Vandel Holdings</span>
    </div>
  </section>
</body>
</html>
```